business card for a massage therapy practice named 'Cedar and Willow Massage Studio'

I really need a trendy, yet easy on the eyes business card to complement my logo. Ideally with some gold or rose gold foil work.

My uploaded file of the logo I have in horizontal but I have a vertical version as well. Another color that is used in the website is a blush pink here and there. I'd like to see some trendy tropical leaves in the design.

```html
<!DOCTYPE html>
<html lang="en">
<head>
<meta charset="utf-8">
<title>Cedar and Willow Massage Studio – Business Card</title>
<link rel="stylesheet" href="https://fonts.googleapis.com/css2?family=Amatic+SC:wght@700&family=Didact+Gothic&family=Open+Sans:wght@700&display=swap">
<style>
  :root {
    --backdrop: #ece9e4;
    --card-gold: #9a8560;
    --gold-decor: #ab9773;
    --card-white: #f7f8fa;
    --ink-white: #ffffff;
    --ink-gold: #9a7f55;
    --ink-grey: #4d4d4d;
    --decor-light: #e3ded4;
  }
  * { margin: 0; padding: 0; box-sizing: border-box; }
  html, body {
    width: 1200px;
    height: 960px;
    overflow: hidden;
    background: var(--backdrop);
  }
  .stage { position: relative; width: 1200px; height: 960px; }

  .card {
    position: absolute;
    left: 270px;
    width: 664px;
    height: 380px;
    overflow: hidden;
    box-shadow: 0 6px 14px rgba(0, 0, 0, 0.18);
  }
  .card--front { top: 72px; background: var(--card-gold); }
  .card--back { top: 509px; background: var(--card-white); }

  .decor-panel {
    position: absolute;
    top: 0;
    right: 0;
    width: 190px;
    height: 380px;
  }
  .card--front .decor-panel {
    background: linear-gradient(180deg, rgba(171,151,115,0.55) 0%, rgba(171,151,115,0.9) 60%, rgba(171,151,115,0.7) 100%);
  }
  .card--back .decor-panel {
    background: linear-gradient(180deg, rgba(227,222,212,0.5) 0%, rgba(227,222,212,0.95) 60%, rgba(227,222,212,0.8) 100%);
  }

  .brand {
    position: absolute;
    left: 155px;
    top: 110px;
    display: flex;
    align-items: center;
    gap: 18px;
    color: var(--ink-white);
    font-family: "Didact Gothic", "Century Gothic", sans-serif;
  }
  .brand__dot {
    width: 46px;
    height: 46px;
    border-radius: 50%;
    background: var(--ink-white);
    flex: none;
  }
  .brand__name {
    font-size: 34px;
    line-height: 1.2;
    letter-spacing: 1px;
  }

  .front__web {
    position: absolute;
    left: 0;
    width: 690px;
    top: 317px;
    text-align: center;
    color: var(--ink-white);
    font-family: "Open Sans", Arial, sans-serif;
    font-weight: 700;
    font-size: 16px;
    letter-spacing: 0.3px;
  }

  .person {
    position: absolute;
    left: 52px;
    top: 155px;
  }
  .person__name {
    font-family: "Amatic SC", "Century Gothic", sans-serif;
    font-weight: 700;
    font-size: 40px;
    line-height: 1;
    color: var(--ink-gold);
    letter-spacing: 1px;
  }
  .person__role {
    margin-top: 4px;
    font-family: "Didact Gothic", "Century Gothic", sans-serif;
    font-size: 21px;
    color: var(--ink-grey);
    letter-spacing: 1px;
  }

  .contact {
    position: absolute;
    left: 52px;
    top: 253px;
    list-style: none;
    font-family: "Didact Gothic", "Century Gothic", sans-serif;
    font-size: 18px;
    line-height: 28.5px;
    color: var(--ink-grey);
  }
  .contact__label { color: var(--ink-gold); }
</style>
</head>
<body>
<main class="stage">
  <section class="card card--front" aria-label="Card front">
    <div class="decor-panel" role="img" aria-label="Faint large brand decoration"></div>
    <div class="brand">
      <span class="brand__dot"></span>
      <span class="brand__name">Cedar and Willow<br>Massage Studio</span>
    </div>
    <p class="front__web">www.cedarwillow.com</p>
  </section>

  <section class="card card--back" aria-label="Card back">
    <div class="decor-panel" role="img" aria-label="Faint large brand decoration"></div>
    <div class="person">
      <h1 class="person__name">Clara Reed</h1>
      <p class="person__role">Artist</p>
    </div>
    <ul class="contact">
      <li><span class="contact__label">Phone:</span> +1 555 014 2290</li>
      <li><span class="contact__label">Email:</span> hello@cedarwillow.com</li>
      <li><span class="contact__label">Web:</span> www.cedarwillow.com</li>
    </ul>
  </section>
</main>
</body>
</html>
```